NZ First of it's kind solutions directory and marketplace for busy Mums needs a business card design

We need a business card design for our new nationwide business in NZ (long term plans to go global). We provide solutions to the everyday challenges that busy Mums face by connecting them with quality communities and suppliers of carefully selected, relevant products and services. We sell direct via our online marketplace. The final design should communicate our values of inclusivity, quality and smart solutions. Colours should incorporate our logo colour palette of #477077 and #6ba8b2. Our website is at https://www.brightnestmums.example

Target Market(s)

busy Mums, Age 28 – 50, female, income over $100K, location main centres NZ primarily but NZ wide. Is likely juggling work or career with a young family. Probably had hobbies which have fallen by the wayside.
-Wants to succeed in her chosen career without compromising on family life
-to successfully juggle her career without feeling like she is compromising her children
- Is time poor, something always has to give and it’s generally her health (she’ll stay up late, get stressed)
- probably ex corporate or professional career. Has discretional income

Industry/Entity Type

Business

Contact Information for Business Card

Lena Forbisher, Founder, BrightNestMums.example (Strapline Tap; Gather; Sorted), 47 Kowhai Terrace, Ellerslie, Auckland 1051, New Zealand. Mob: 021 483 517 Ph: +64 (0)9 571 4860

Font styles to use
Other font styles liked:
• Raleway, and/or Architects Daughter

Colors
00a990
33b8a4
86cfc6
cfeae6

Requirements
Must have
• the above details, streamline. the logo and colours associated with those logos
Should not have
• foil or metallic colours

```html
<!DOCTYPE html>
<html lang="en">
<head>
<meta charset="utf-8">
<title>BrightNestMums Business Card</title>
<link rel="stylesheet" href="https://fonts.googleapis.com/css2?family=Roboto:wght@400;500;700&display=swap">
<style>
  :root {
    --brand-dark: #477077;
    --brand-light: #6ba8b2;
    --ink-muted: #5b7e84;
    --card-white: #ffffff;
    --page-bg: #e7eaeb;
    --photo-warm: #c98a4a;
    --photo-cream: #e9dccb;
    --photo-grey: #6f7478;
    --photo-shadow: #4a4c4f;
  }
  * { box-sizing: border-box; margin: 0; padding: 0; }
  html, body {
    width: 1200px; height: 896px; overflow: hidden;
    background: var(--page-bg);
    font-family: "Roboto", Arial, sans-serif;
  }
  .canvas { position: relative; width: 1200px; height: 896px; }
  .card {
    position: absolute; left: 290px;
    width: 620px; height: 354px;
    border-radius: 22px; overflow: hidden;
    box-shadow: 0 10px 30px rgba(0,0,0,0.18);
  }
  .card--front { top: 70px; }
  .card--back { top: 472px; background: var(--card-white); }

  /* Front */
  .front-photo {
    position: absolute; inset: 0;
    background:
      radial-gradient(ellipse 40% 55% at 38% 55%, rgba(201,138,74,0.9), transparent 70%),
      radial-gradient(ellipse 50% 40% at 70% 30%, rgba(233,220,203,0.85), transparent 70%),
      linear-gradient(135deg, var(--photo-grey) 0%, var(--photo-cream) 45%, var(--photo-warm) 65%, var(--photo-shadow) 100%);
  }
  .front-veil {
    position: absolute; inset: 0;
    background: linear-gradient(90deg, rgba(40,42,45,0.35), rgba(40,42,45,0.1) 60%, rgba(40,42,45,0.3));
  }
  .front-brand {
    position: absolute; left: 70px; top: 140px;
    display: flex; align-items: center; gap: 16px;
    color: var(--card-white);
  }
  .brand-dot {
    width: 40px; height: 40px; border-radius: 50%;
    background: var(--card-white);
    flex: none;
  }
  .brand-name { white-space: nowrap; }
  .front-brand .brand-name { font-size: 60px; font-weight: 700; letter-spacing: -1px; }
  .front-web {
    position: absolute; right: 50px; bottom: 40px;
    color: var(--card-white); font-size: 17px; letter-spacing: 0.3px;
  }

  /* Back */
  .back-brand {
    position: absolute; left: 40px; top: 158px;
    display: flex; align-items: center; gap: 10px;
    color: var(--brand-light);
  }
  .back-brand .brand-dot { width: 26px; height: 26px; background: var(--brand-light); }
  .back-brand .brand-name { font-size: 28px; font-weight: 700; letter-spacing: -0.5px; }
  .divider {
    position: absolute; left: 340px; top: 60px;
    width: 2px; height: 234px; background: var(--brand-dark);
  }
  .contact {
    position: absolute; left: 362px; top: 64px; right: 30px;
    color: var(--ink-muted);
  }
  .contact .person-name {
    font-size: 28px; font-weight: 700; color: var(--brand-dark);
    line-height: 1.1;
  }
  .contact .role { font-size: 15px; margin-top: 4px; margin-bottom: 22px; }
  .contact .address { font-size: 15px; line-height: 1.5; margin-bottom: 14px; }
  .contact-line {
    display: flex; align-items: center; gap: 8px;
    font-size: 15px; line-height: 1.6; white-space: nowrap;
  }
  .contact-line svg { width: 11px; height: 11px; flex: none; fill: var(--ink-muted); }
</style>
</head>
<body>
<main class="canvas">
  <section class="card card--front">
    <div class="front-photo" role="img" aria-label="Soft warm photograph of a relaxed mother resting by a bright window"></div>
    <div class="front-veil"></div>
    <div class="front-brand">
      <span class="brand-dot"></span>
      <span class="brand-name">BrightNestMums</span>
    </div>
    <p class="front-web">www.brightnestmums.example</p>
  </section>

  <section class="card card--back">
    <div class="back-brand">
      <span class="brand-dot"></span>
      <span class="brand-name">BrightNestMums</span>
    </div>
    <div class="divider"></div>
    <div class="contact">
      <h1 class="person-name">Lena Forbisher</h1>
      <p class="role">Founder</p>
      <p class="address">47 Kowhai Terrace, Ellerslie<br>Auckland 1051, New Zealand</p>
      <p class="contact-line">
        <svg viewBox="0 0 12 12" aria-hidden="true"><rect x="3" y="0.5" width="6" height="11" rx="1.2"/><rect x="4" y="2" width="4" height="7" fill="#fff"/></svg>
        021 483 517
      </p>
      <p class="contact-line">
        <svg viewBox="0 0 12 12" aria-hidden="true"><path d="M2.5 1 L4.5 1 L5.3 3.5 L4 4.6 C4.7 6.2 5.8 7.3 7.4 8 L8.5 6.7 L11 7.5 L11 9.5 C11 10.3 10.3 11 9.5 11 C5 11 1 7 1 2.5 C1 1.7 1.7 1 2.5 1 Z"/></svg>
        +64 (0)9 571 4860
      </p>
      <p class="contact-line">
        <svg viewBox="0 0 12 12" aria-hidden="true"><circle cx="6" cy="6" r="5.5"/><path d="M0.5 6 H11.5 M6 0.5 C3.5 3 3.5 9 6 11.5 C8.5 9 8.5 3 6 0.5" stroke="#fff" stroke-width="0.9" fill="none"/></svg>
        www.brightnestmums.example
      </p>
    </div>
  </section>
</main>
</body>
</html>
```